I am looking to create a newly designed website for our national leadership conference which is entitled, "The Harbor of Momentum Leadership Summit". The Harbor of Momentum Leadership Summit is a national conference for student leaders that prepares them for career leadership success. The current website can be seen at www.harborofmomentumleadershipsummit.com.

My goal for the new site is to create a more updated, fresh, hip, and exciting look that appeals to the younger generation while also maintaining are professional appeal. The color should be black, white, and gold. We want there to be live videos played and places to insert pictures for the panels as well.

I look forward to seeing you the new creations.

Requirements
Must have
• Ability to play videos on the home page and throughout the website. Also, make sure that the website shows up clearly on an zTablet.
Nice to have
• Nice look

```html
<!DOCTYPE html>
<html lang="en">
<head>
<meta charset="utf-8">
<title>Harbor of Momentum Leadership Summit</title>
<link href="https://fonts.googleapis.com/css2?family=Open+Sans:wght@400;600&family=Roboto+Condensed:wght@300;400;700&display=swap" rel="stylesheet">
<style>
:root{
  --gold:#fdd163;
  --gold-deep:#f0b83a;
  --orange:#f08a14;
  --orange-dark:#d76c05;
  --ink:#333333;
  --muted:#6b6b6b;
  --dark:#2b2622;
  --black:#0f0f10;
  --white:#ffffff;
  --line:#e4e4e4;
}
*{margin:0;padding:0;box-sizing:border-box}
html,body{width:1200px;height:2757px;overflow:hidden}
body{position:relative;background:var(--white);font-family:"Open Sans",Arial,sans-serif;color:var(--ink)}
.abs{position:absolute}
.heading{font-family:"Roboto Condensed",Arial Narrow,sans-serif;font-weight:400;text-transform:uppercase;letter-spacing:.5px}

/* header */
.site-header{position:absolute;left:0;top:0;width:1200px;height:84px;background:var(--gold);z-index:3}
.logo-tab{position:absolute;left:0;top:0;width:1200px;height:134px;z-index:3}
.nav{position:absolute;top:0;height:84px;display:flex;font-family:"Roboto Condensed",sans-serif;font-size:13px;text-transform:uppercase;color:#3a2e12}
.nav a{display:flex;align-items:center;height:84px;padding:0 24px;border-right:1px solid rgba(0,0,0,.08);color:inherit;text-decoration:none}
.nav a:first-child{border-left:1px solid rgba(0,0,0,.08)}
.nav-left{left:73px}
.nav-right{left:700px}
.nav .active{position:relative}
.nav .active::after{content:"";position:absolute;left:22px;right:22px;top:52px;height:6px;border-bottom:2px solid #3a2e12;border-radius:0 0 50% 50%}
.brand{position:absolute;left:440px;top:26px;width:320px;z-index:4;text-align:center}
.brand-dot{width:44px;height:44px;border-radius:50%;background:var(--orange);margin:0 auto 8px}
.brand-name{font-family:"Roboto Condensed",sans-serif;font-weight:700;font-size:19px;color:#2a2a2a;text-transform:uppercase}

/* hero */
.hero{position:absolute;left:0;top:84px;width:1200px;height:561px;background:linear-gradient(90deg,#3b4257 0%,#5a3a2e 30%,#9a5a3c 60%,#7c3c2a 100%)}
.hero-title{position:absolute;left:628px;top:305px;font-size:54px;color:var(--white);font-weight:700}
.hero-text{position:absolute;left:630px;top:378px;width:420px;font-size:15px;line-height:22px;color:#f3e3c2}
.hero-btn{position:absolute;left:628px;top:437px;width:170px;height:44px;border:2px solid var(--white);border-radius:22px;background:var(--gold);color:#3a2e12;font-family:"Roboto Condensed",sans-serif;font-size:15px;text-transform:uppercase;display:flex;align-items:center;justify-content:center}
.hero-arrow{position:absolute;top:358px}

/* features */
.features{position:absolute;left:0;top:645px;width:1200px;height:362px;background:linear-gradient(180deg,#f3f1ef,#ebe6e1)}
.feature{position:absolute;top:76px;width:300px;text-align:center}
.feature-icon{width:114px;height:114px;border-radius:50%;background:var(--orange);margin:0 auto;box-shadow:inset -10px -10px 0 var(--orange-dark);display:flex;align-items:center;justify-content:center}
.feature-title{margin-top:20px;font-size:19px;color:#3d3d3d}
.feature-text{margin:10px auto 0;width:270px;font-size:11.5px;line-height:21px;color:var(--muted)}

/* videos */
.videos{position:absolute;left:0;top:1007px;width:1200px;height:546px;background:var(--gold)}
.section-title{position:absolute;left:0;width:1200px;text-align:center;font-size:40px;color:#3a3328}
.videos-intro{position:absolute;left:190px;top:101px;width:820px;text-align:center;font-size:12px;line-height:22px;color:#3a3328}
.video-card{position:absolute;top:173px;width:314px}
.video-media{position:relative;height:217px;background:linear-gradient(160deg,#7a6a5e,#2f2a28)}
.video-bar{position:absolute;left:0;top:0;width:100%;height:35px;background:rgba(40,40,40,.75);color:var(--white);font-size:11px;display:flex;align-items:center;justify-content:space-between;padding:0 14px;text-transform:uppercase}
.play{position:absolute;left:133px;top:92px}
.video-title{margin-top:20px;font-family:"Roboto Condensed",sans-serif;font-size:15px;text-transform:uppercase;color:#3a3328}
.video-text{margin-top:10px;width:250px;font-size:11px;line-height:21px;color:#3a3328}
.video-go{position:absolute;right:2px;top:274px}

/* register */
.register{position:absolute;left:0;top:1553px;width:1200px;height:371px;background:linear-gradient(180deg,#f1efec,#e6e1dc)}
.divider{position:absolute;left:455px;width:290px;height:14px}
.register-text{position:absolute;left:150px;top:170px;width:900px;text-align:center;font-size:14px;line-height:26px;color:#555}
.register-btn{position:absolute;left:496px;top:250px;width:208px;height:44px;border-radius:22px;background:var(--gold-deep);box-shadow:0 3px 0 #c8931f;font-family:"Roboto Condensed",sans-serif;font-size:16px;text-transform:uppercase;color:#3a2e12;display:flex;align-items:center;justify-content:center}

/* countdown */
.countdown{position:absolute;left:0;top:1924px;width:1200px;height:358px;background:linear-gradient(90deg,#2e2823,#3b332c 50%,#231e1b)}
.count-title{top:60px;color:var(--white)}
.count-unit{position:absolute;top:149px;width:118px;text-align:center}
.count-ring{width:118px;height:118px;border-radius:50%;border:4px solid var(--white);display:flex;align-items:center;justify-content:center;font-family:"Roboto Condensed",sans-serif;font-size:42px;color:var(--gold)}
.count-ring.gold{border-color:var(--gold)}
.count-label{margin-top:10px;font-size:19px;color:var(--white);font-family:"Roboto Condensed",sans-serif}

/* partners */
.partners{position:absolute;left:0;top:2282px;width:1200px;height:359px;background:var(--white)}
.partners-title{top:50px;font-size:31px}
.partners-text{position:absolute;left:300px;top:102px;width:600px;text-align:center;font-size:12px;line-height:22px;color:#666}
.partner{position:absolute;top:215px;width:156px;height:76px;border:1px solid var(--line);display:flex;align-items:center;justify-content:center;font-family:"Roboto Condensed",sans-serif;font-weight:700;font-size:17px;color:#5a5a5a;text-align:center;line-height:18px}
.side-arrow{position:absolute;top:105px}

/* footer */
.site-footer{position:absolute;left:0;top:2641px;width:1200px;height:116px;background:var(--black)}
.social{position:absolute;top:23px;width:30px;height:30px;border-radius:50%;background:var(--white)}
.copyright{position:absolute;left:0;top:70px;width:1200px;text-align:center;font-size:11.5px;color:#dcdcdc}
</style>
</head>
<body>

<header class="site-header">
  <nav class="nav nav-left">
    <a class="active">Home</a><a>About Us</a><a>Conference</a><a>Register</a>
  </nav>
  <nav class="nav nav-right">
    <a>Y Factor</a><a>Testimonials</a><a>Videos</a><a>Contact</a>
  </nav>
</header>
<svg class="logo-tab" viewBox="0 0 1200 134" aria-hidden="true"><polygon points="395,0 808,0 808,84 760,134 440,134 395,84" fill="#fdd163"/></svg>
<div class="brand">
  <div class="brand-dot"></div>
  <div class="brand-name">Harbor of Momentum</div>
</div>

<section class="hero">
  <div class="abs" role="img" aria-label="Speaker at a podium facing a large conference audience" style="inset:0"></div>
  <h1 class="hero-title heading">Harbor of Momentum</h1>
  <p class="hero-text">Leadership Conference is a national conference for student leaders that prepares them for career leadership success</p>
  <div class="hero-btn">Read More Info</div>
  <svg class="hero-arrow" style="left:48px" width="30" height="60" viewBox="0 0 30 60"><polyline points="26,2 4,30 26,58" fill="none" stroke="rgba(255,255,255,.6)" stroke-width="2"/></svg>
  <svg class="hero-arrow" style="left:1138px" width="30" height="60" viewBox="0 0 30 60"><polyline points="4,2 26,30 4,58" fill="none" stroke="rgba(255,255,255,.6)" stroke-width="2"/></svg>
</section>

<section class="features">
  <div class="feature" style="left:94px">
    <div class="feature-icon"><svg width="44" height="56" viewBox="0 0 44 56"><circle cx="22" cy="8" r="7" fill="#fff"/><rect x="8" y="20" width="28" height="6" fill="#fff"/><rect x="14" y="26" width="16" height="28" fill="#fff"/></svg></div>
    <h3 class="feature-title">Leadership Conference</h3>
    <p class="feature-text">Lorem ipsum dolor sit amet, consectetur adipising elit, sed do eiusmod tempor iunt ut labore et dolore magna aliqua. eiusmod</p>
  </div>
  <div class="feature" style="left:444px">
    <div class="feature-icon"><svg width="60" height="50" viewBox="0 0 60 50"><circle cx="16" cy="8" r="6" fill="#fff"/><circle cx="44" cy="8" r="6" fill="#fff"/><rect x="10" y="16" width="12" height="16" fill="#fff"/><rect x="38" y="16" width="12" height="16" fill="#fff"/><rect x="4" y="26" width="52" height="5" fill="#fff"/><rect x="10" y="31" width="4" height="17" fill="#fff"/><rect x="46" y="31" width="4" height="17" fill="#fff"/></svg></div>
    <h3 class="feature-title">Student leaders</h3>
    <p class="feature-text">Lorem ipsum dolor sit amet, consectetur adipising elit, sed do eiusmod tempor iunt ut labore et dolore magna aliqua. eiusmod</p>
  </div>
  <div class="feature" style="left:798px">
    <div class="feature-icon"><svg width="56" height="56" viewBox="0 0 56 56"><circle cx="22" cy="22" r="17" fill="none" stroke="#fff" stroke-width="3"/><ellipse cx="22" cy="22" rx="7" ry="17" fill="none" stroke="#fff" stroke-width="2"/><line x1="5" y1="22" x2="39" y2="22" stroke="#fff" stroke-width="2"/><line x1="35" y1="35" x2="52" y2="52" stroke="#fff" stroke-width="6" stroke-linecap="round"/></svg></div>
    <h3 class="feature-title">Career Leadership</h3>
    <p class="feature-text">Lorem ipsum dolor sit amet, consectetur adipising elit, sed do eiusmod tempor iunt ut labore et dolore magna aliqua. eiusmod</p>
  </div>
</section>

<section class="videos">
  <h2 class="section-title heading" style="top:44px">Conference Video</h2>
  <p class="videos-intro">Lorem ipsum dolor sit amet, consectetur adipiscing elit, sed do eiusmod tempor incididunt ut labore et dolore magna aliqua. Ut enim ad minim veniam, quis nostrud exercitation ullamco laboris nisi ut aliquip ex ea commodo consequat. Duis aute irure dolor in reprehenderit</p>

  <article class="video-card" style="left:99px">
    <div class="video-media" role="img" aria-label="Video still of conference guests posing together">
      <div class="video-bar"><span>Voted as top student leadership</span><svg width="12" height="12" viewBox="0 0 12 12"><circle cx="9" cy="2.5" r="2" fill="#fff"/><circle cx="3" cy="6" r="2" fill="#fff"/><circle cx="9" cy="9.5" r="2" fill="#fff"/><polyline points="9,2.5 3,6 9,9.5" fill="none" stroke="#fff"/></svg></div>
      <svg class="play" width="48" height="34" viewBox="0 0 48 34"><rect x="1" y="1" width="46" height="32" rx="8" fill="rgba(0,0,0,.55)" stroke="#fff" stroke-width="2"/><polygon points="19,10 31,17 19,24" fill="#fff"/></svg>
    </div>
    <h4 class="video-title">Duis aute irure dolor in</h4>
    <p class="video-text">Lorem ipsum dolor sit amet, consectetur ading elit, sed do eiusmod tempor incididunt</p>
    <svg class="video-go" width="30" height="30" viewBox="0 0 30 30"><circle cx="15" cy="15" r="13" fill="none" stroke="#2a2a2a" stroke-width="2"/><polyline points="12,9 18,15 12,21" fill="none" stroke="#2a2a2a" stroke-width="2"/></svg>
  </article>

  <article class="video-card" style="left:441px">
    <div class="video-media" role="img" aria-label="Video still of a speaker addressing the conference">
      <div class="video-bar"><span>Voted as top student leadership</span><svg width="12" height="12" viewBox="0 0 12 12"><circle cx="9" cy="2.5" r="2" fill="#fff"/><circle cx="3" cy="6" r="2" fill="#fff"/><circle cx="9" cy="9.5" r="2" fill="#fff"/><polyline points="9,2.5 3,6 9,9.5" fill="none" stroke="#fff"/></svg></div>
      <svg class="play" width="48" height="34" viewBox="0 0 48 34"><rect x="1" y="1" width="46" height="32" rx="8" fill="rgba(0,0,0,.55)" stroke="#fff" stroke-width="2"/><polygon points="19,10 31,17 19,24" fill="#fff"/></svg>
    </div>
    <h4 class="video-title">Duis aute irure dolor in</h4>
    <p class="video-text">Lorem ipsum dolor sit amet, consectetur ading elit, sed do eiusmod tempor incididunt</p>
    <svg class="video-go" width="30" height="30" viewBox="0 0 30 30"><circle cx="15" cy="15" r="13" fill="none" stroke="#2a2a2a" stroke-width="2"/><polyline points="12,9 18,15 12,21" fill="none" stroke="#2a2a2a" stroke-width="2"/></svg>
  </article>

  <article class="video-card" style="left:785px">
    <div class="video-media" role="img" aria-label="Video still of two student attendees smiling">
      <div class="video-bar"><span>Voted as top student leadership</span><svg width="12" height="12" viewBox="0 0 12 12"><circle cx="9" cy="2.5" r="2" fill="#fff"/><circle cx="3" cy="6" r="2" fill="#fff"/><circle cx="9" cy="9.5" r="2" fill="#fff"/><polyline points="9,2.5 3,6 9,9.5" fill="none" stroke="#fff"/></svg></div>
      <svg class="play" width="48" height="34" viewBox="0 0 48 34"><rect x="1" y="1" width="46" height="32" rx="8" fill="rgba(0,0,0,.55)" stroke="#fff" stroke-width="2"/><polygon points="19,10 31,17 19,24" fill="#fff"/></svg>
    </div>
    <h4 class="video-title">Duis aute irure dolor in</h4>
    <p class="video-text">Lorem ipsum dolor sit amet, consectetur ading elit, sed do eiusmod tempor incididunt</p>
    <svg class="video-go" width="30" height="30" viewBox="0 0 30 30"><circle cx="15" cy="15" r="13" fill="none" stroke="#2a2a2a" stroke-width="2"/><polyline points="12,9 18,15 12,21" fill="none" stroke="#2a2a2a" stroke-width="2"/></svg>
  </article>
</section>

<section class="register">
  <h2 class="section-title heading" style="top:74px;color:#3d3d3d">Register Now!</h2>
  <svg class="divider" style="top:127px" viewBox="0 0 290 14"><line x1="0" y1="7" x2="290" y2="7" stroke="#d7d2cc"/><rect x="128" y="0" width="34" height="14" fill="#ece8e4"/><path d="M132,5 q6,-4 12,0 t12,0 M132,10 q6,-4 12,0 t12,0" fill="none" stroke="#9a948d" stroke-width="1.2"/></svg>
  <p class="register-text">for a transformational leadership experience that will connect you with an incredible diverse leadership network of students and professionals that provide you with the inspiration and leadership/professional skills needed to take your life to the next level!</p>
  <div class="register-btn">Register Now!</div>
</section>

<section class="countdown">
  <div class="abs" role="img" aria-label="Speaker holding a microphone in front of a seated audience" style="inset:0"></div>
  <h2 class="section-title heading count-title">6th Annual Conference Countdown</h2>
  <div class="count-unit" style="left:356px"><div class="count-ring">12</div><div class="count-label">Hours</div></div>
  <div class="count-unit" style="left:544px"><div class="count-ring gold">20</div><div class="count-label">Minutes</div></div>
  <div class="count-unit" style="left:724px"><div class="count-ring" style="color:#fff">30</div><div class="count-label">Seconds</div></div>
</section>

<section class="partners">
  <h2 class="section-title heading partners-title" style="color:#333">Network with Executives</h2>
  <p class="partners-text">Partnered with the worlds leading Smart technology companies our products capabilities and reliability are proven and competitive in the most demanding markets.</p>
  <svg class="divider" style="top:166px" viewBox="0 0 290 14"><path d="M128,5 q6,-4 12,0 t12,0 M128,10 q6,-4 12,0 t12,0" fill="none" stroke="#b5b5b5" stroke-width="1.2"/></svg>
  <svg class="side-arrow" style="left:96px" width="36" height="36" viewBox="0 0 36 36"><circle cx="18" cy="18" r="16" fill="none" stroke="#e2e2e2" stroke-width="2"/><polyline points="21,11 14,18 21,25" fill="none" stroke="#cfcfcf" stroke-width="2"/></svg>
  <svg class="side-arrow" style="left:1066px" width="36" height="36" viewBox="0 0 36 36"><circle cx="18" cy="18" r="16" fill="none" stroke="#e2e2e2" stroke-width="2"/><polyline points="15,11 22,18 15,25" fill="none" stroke="#cfcfcf" stroke-width="2"/></svg>
  <div class="partner" style="left:99px">Halden Park</div>
  <div class="partner" style="left:268px">Brightwave Sound</div>
  <div class="partner" style="left:437px">Fizzlane</div>
  <div class="partner" style="left:608px">Ridgecrest State</div>
  <div class="partner" style="left:777px">Coastline University</div>
  <div class="partner" style="left:948px">Marrow Hall</div>
</section>

<footer class="site-footer">
  <span class="social" style="left:523px" aria-label="Social link"></span>
  <span class="social" style="left:566px" aria-label="Social link"></span>
  <span class="social" style="left:606px" aria-label="Social link"></span>
  <span class="social" style="left:647px" aria-label="Social link"></span>
  <p class="copyright">© Copyright 2015 Harbor of Momentum. All Rights Reserved.</p>
</footer>

</body>
</html>
```